Velvet Riot Rising Line of Sparkling Wine & Spirits

Back info: Nora Beth Quill Owner 555-318-4402 1480 E. Harlow Ave, Bldg. 2, & 3, Fairhaven Ca. 95871
Sparkling Wines & Memorabilia www.velvetriotrising.com
Ok I have uploaded the winning design. The color that I am after is the Fushia, Raspberry, Red, Matte Satin Matalic Finish. With a 24 Karet Gold color Foil. The Bottle is on the top row and it's the 2nd Bottle in. That is the Color that I want. This is the style of font. Make sure that you put what we're advertising. Good Luck to you all. Warmest regards, Nora
21 & up UniSex
Sparkling Wine and Memorabilia
there listed up above.....

```html
<!DOCTYPE html>
<html lang="en">
<head>
<meta charset="utf-8">
<title>Velvet Riot Rising – Business Card</title>
<link href="https://fonts.googleapis.com/css2?family=Arimo:wght@400;700&display=swap" rel="stylesheet">
<style>
  :root {
    --fuchsia: #e0157f;
    --fuchsia-deep: #a8105f;
    --gold: #e2b24f;
    --rule-brown: #7a2a1e;
    --ink: #444444;
    --ink-dark: #2f2f2f;
    --backdrop: #e6e6e6;
    --card: #ffffff;
    --grey-dark: #555555;
  }
  * { margin: 0; padding: 0; box-sizing: border-box; }
  html, body { width: 1200px; height: 1200px; overflow: hidden; }
  body {
    background: var(--backdrop);
    font-family: "Arimo", Arial, sans-serif;
    position: relative;
  }
  .card {
    position: absolute;
    left: 264px;
    width: 690px;
    height: 392px;
    background: var(--card);
    box-shadow: 0 10px 24px rgba(0,0,0,0.18);
    overflow: hidden;
  }
  .card--front { top: 159px; }
  .card--back {
    top: 654px;
    background: linear-gradient(to bottom, #ffffff 0%, #ffffff 45%, #cfcfcf 62%, #9a9a9a 82%, var(--grey-dark) 100%);
  }

  .bottle {
    position: absolute;
    border-radius: 16px 16px 6px 6px;
    background: linear-gradient(to right, var(--fuchsia-deep), var(--fuchsia) 45%, var(--fuchsia-deep));
  }
  .card--front .bottle { left: 173px; top: 92px; width: 66px; height: 210px; }
  .card--back .bottle { left: 98px; top: 57px; width: 72px; height: 243px; }

  .divider {
    position: absolute;
    left: 267px; top: 90px;
    width: 1px; height: 218px;
    background: #d6d6d6;
  }
  .details { position: absolute; left: 291px; top: 110px; color: var(--ink); }
  .details__name {
    color: var(--fuchsia);
    font-weight: 700;
    font-size: 26px;
    letter-spacing: 0.3px;
    line-height: 1;
  }
  .details__role { color: var(--gold); font-size: 17px; margin-top: 4px; margin-left: -2px; }
  .details__address { font-size: 16px; line-height: 21px; margin-top: 22px; }
  .details__contact { list-style: none; font-size: 16px; line-height: 21px; margin-top: 22px; }
  .details__contact li { display: flex; align-items: center; gap: 12px; }
  .details__contact svg { width: 14px; height: 14px; flex: none; }

  .rule-thin {
    position: absolute; left: 0; right: 0; top: 371px; height: 2px;
    background: var(--rule-brown);
  }
  .rule-band {
    position: absolute; left: 0; right: 0; bottom: 0; height: 17px;
    background: linear-gradient(to right, var(--fuchsia-deep), var(--fuchsia) 50%, var(--fuchsia-deep));
  }

  .brand { position: absolute; left: 190px; top: 162px; }
  .brand__name {
    font-weight: 700;
    font-size: 43px;
    color: var(--ink-dark);
    line-height: 1;
    white-space: nowrap;
  }
  .brand__rule {
    position: absolute; left: -15px; top: 64px;
    width: 426px; height: 1px;
    background: linear-gradient(to right, #9a9a9a, #9a9a9a 70%, rgba(154,154,154,0));
  }
  .brand__tagline {
    position: absolute; left: 0; top: 75px;
    font-size: 17px; letter-spacing: 2.2px; white-space: nowrap;
    color: var(--ink-dark);
  }
  .brand__tagline em { font-style: normal; font-weight: 700; color: var(--fuchsia); }
  .edge-line {
    position: absolute; left: 0; right: 0; bottom: 0; height: 2px;
    background: var(--fuchsia);
  }
</style>
</head>
<body>

<section class="card card--front">
  <div class="bottle" role="img" aria-label="Fuchsia sparkling wine bottle with gold foil neck and crest label"></div>
  <div class="divider"></div>
  <div class="details">
    <h1 class="details__name">NORA BETH QUILL</h1>
    <p class="details__role">Owner</p>
    <p class="details__address">E. Harlow Ave<br>Bldg. 2, &amp; 3, Fairhaven Ca. 95871</p>
    <ul class="details__contact">
      <li>
        <svg viewBox="0 0 24 24" aria-hidden="true"><path fill="#e0157f" d="M6.6 10.8a15.1 15.1 0 0 0 6.6 6.6l2.2-2.2c.3-.3.7-.4 1-.2 1.1.4 2.3.6 3.6.6.6 0 1 .4 1 1V20c0 .6-.4 1-1 1A17 17 0 0 1 3 4c0-.6.4-1 1-1h3.5c.6 0 1 .4 1 1 0 1.3.2 2.5.6 3.6.1.3 0 .7-.2 1z"/></svg>
        <span>555-318-4402 1480</span>
      </li>
      <li>
        <svg viewBox="0 0 24 24" aria-hidden="true"><circle cx="12" cy="12" r="10" fill="#e0157f"/><path fill="#fff" d="M7 7c2 0 3 1 3 2.5S8 11 8 12.5 9.5 15 9 17c-2-.8-3.5-3-3.5-5.5 0-1.7.6-3.3 1.5-4.5zm8 1c1.5 0 2.5 1 2 2.5s-2 1-2.5 2.5 1 2.5.5 4c1.800-1.2 3-3.2 3-5.5 0-1.300-.3-2.5-.9-3.500z"/></svg>
        <span>www.velvetriotrising.com</span>
      </li>
    </ul>
  </div>
  <div class="rule-thin"></div>
  <div class="rule-band"></div>
</section>

<section class="card card--back">
  <div class="bottle" role="img" aria-label="Fuchsia sparkling wine bottle with gold foil neck and crest label"></div>
  <div class="brand">
    <h2 class="brand__name">Velvet Riot Rising</h2>
    <div class="brand__rule"></div>
    <p class="brand__tagline">SPARKLING <em>WINES &amp; MEMORABILIA</em></p>
  </div>
  <div class="edge-line"></div>
</section>

</body>
</html>
```